Fine Art business needs new website

We need a simple website with a home page, about us page, New sculptures, Sold sculptures, and a contact us page.Our sculptures are very high end one of a kind pieces. As such we need the site to be VERY elegant and professional. Lastly, because I'll be updating pictures on the website on a monthly basis it needs to be user friendly to update (Wordpress is preferred). The only branding we have so far for the business is a business card.
Updates
I wasn't completely ready when this project launched, also I am on the road right now and haven't been able to be as responsive to all you designers as I would like. I will work on giving feedback to all the top designs we've received so far. Thank you all so much for your participation and hardwork.
Target Market(s)
High end customers (affluent), art collectors, interior decorators/designers
Industry/Entity Type
Art Gallery
Coding
Coded - Design and coding required
Number of Pages Required
5+ page
Requirements
Must have
- Easily editable picture gallery for myself so that I can add new pieces(pictures of the pieces), remove sold pieces, etc. I would like the website to be built in wordpress so I can update it. I currently use mangewordpress through Netmarro for my other business website and would like to do the same for this one.
- Pages:
- -Intro page with featured pieces
- -Current pieces gallery (for sale) mainly a picture gallery
- -Sculptures archive (sold pieces) another picture gallery
- -About us: Pull-down of -about the artist (attached content)
- -Artistic Process (attached content)
- -Show Schedule:
- -one page dedicated to "friends of TMV" (basically a link page)
- TO BE CLEAR "www.pineroverslane.com" IS A TOTALLY DIFFERENT SITE AND I'M NOT TRYING TO COMBINE THE TWO OR JOIN THEM INTO ONE. This page needs be more elegant and seperate from the Pine Rovers site.
- UPDATE: I'd like a link to the TMV Faceplume page: https://www.faceplume-social.com/mirelcraftworks/
Nice to have
- I would like the pictures on the gallery pages able to have text connected with them (Materials, price)
- I would like the site style and fonts to be similar to our business cards we've already had designed (picture attached).
Should not have
- Too much flash or other things that will make the site slow to load.

```html
<!DOCTYPE html>
<html lang="en">
<head>
<meta charset="utf-8">
<title>Tallus Mineral Vault</title>
<link href="https://fonts.googleapis.com/css2?family=Cormorant+Garamond:wght@400;500&family=Karla:wght@400;500;700&family=Tinos:wght@400;700&display=swap" rel="stylesheet">
<style>
  :root{
    --ink:#111111;
    --muted:#4a4a4a;
    --nav:#222222;
    --band-light:#ddedf4;
    --band-mid:#c8d4ee;
    --band-deep:#9ea6e0;
    --feature-a:#5b48a8;
    --feature-b:#8d83c4;
    --dots:#2f22b8;
    --paper:#ffffff;
  }
  *{margin:0;padding:0;box-sizing:border-box}
  html,body{width:1200px;height:1000px;overflow:hidden;background:var(--paper)}
  body{position:relative;font-family:"Tinos",serif;color:var(--ink)}

  .site-header{position:absolute;top:0;left:0;width:1200px;height:72px}
  .site-logo{position:absolute;left:158px;top:25px;font-family:"Cormorant Garamond",serif;font-size:19px;font-weight:400;letter-spacing:.2px;color:#333;text-decoration:none;white-space:nowrap}
  .main-nav{position:absolute;left:440px;top:28px;display:flex;gap:18px}
  .main-nav a{font-family:"Karla",sans-serif;font-size:13.5px;color:var(--nav);text-decoration:none;letter-spacing:.3px}

  .hero{position:absolute;top:0;left:0;width:1200px;height:540px}
  .hero-ring{position:absolute;left:0;top:0}
  .hero-band{position:absolute;left:0;top:207px;width:1200px;height:253px;
    background:linear-gradient(90deg,var(--band-light) 0%,var(--band-light) 22%,var(--band-mid) 45%,var(--band-deep) 100%)}
  .hero-feature{position:absolute;left:720px;top:207px;width:450px;height:253px;
    background:linear-gradient(90deg,var(--feature-b) 0%,var(--feature-a) 45%,#a99a7a 75%,var(--feature-b) 100%)}
  .hero-title{position:absolute;left:158px;top:176px;font-family:"Cormorant Garamond",serif;font-weight:400;font-size:66px;line-height:82px;letter-spacing:1px;color:#000;white-space:nowrap}
  .hero-contact{position:absolute;left:160px;top:344px;display:flex;gap:14px;font-family:"Karla",sans-serif;font-size:14px;color:#555}
  .hero-contact span{display:flex;align-items:center;gap:4px}
  .hero-button{position:absolute;left:270px;top:393px;width:158px;height:31px;border:1.5px solid #111;display:flex;align-items:center;justify-content:center;font-family:"Karla",sans-serif;font-size:10px;letter-spacing:1.4px;color:#111;text-decoration:none}

  .featured-piece{position:absolute;top:592px;left:0;width:1200px;height:379px}
  .piece-photo{position:absolute;left:0;top:0;width:600px;height:379px;
    background:linear-gradient(135deg,#9b95d4 0%,#b7b8dc 50%,#d3dbe3 100%)}
  .piece-info{position:absolute;left:634px;top:0}
  .piece-title{font-family:"Cormorant Garamond",serif;font-weight:400;font-size:39px;margin-top:24px;letter-spacing:.4px}
  .piece-label{font-family:"Karla",sans-serif;font-weight:700;font-size:14.5px;margin-top:20px}
  .piece-story{font-size:13.6px;line-height:18.6px;color:var(--muted);width:455px;margin-top:13px}
  .piece-materials{font-size:13.6px;color:var(--muted);margin-top:12px}
  .piece-price{font-weight:700;font-size:22px;margin-top:22px}

  .next-piece{position:absolute;left:600px;top:971px;width:600px;height:29px;background:linear-gradient(90deg,#d5dde2,#a8a6dc)}
</style>
</head>
<body>
  <header class="site-header">
    <a class="site-logo" href="#">TALLUS MINERAL VAULT</a>
    <nav class="main-nav">
      <a href="#">Gallery</a>
      <a href="#">Archive</a>
      <a href="#">About</a>
      <a href="#">Artistic Process</a>
      <a href="#">Show Schedule</a>
      <a href="#">Faceplume</a>
      <a href="#">Friends of TMV</a>
    </nav>
  </header>

  <section class="hero">
    <svg class="hero-ring" width="600" height="540" aria-hidden="true">
      <circle cx="292" cy="316" r="210" fill="none" stroke="var(--dots)" stroke-width="2" stroke-dasharray="1.5 3.5" stroke-linecap="round"/>
    </svg>
    <div class="hero-band"></div>
    <div class="hero-feature" role="img" aria-label="Photograph of an amethyst geode sculpture with a natural stone arch"></div>
    <h1 class="hero-title">TALLUS MINERAL<br>VAULT</h1>
    <div class="hero-contact">
      <span><svg width="11" height="12" viewBox="0 0 24 24" aria-hidden="true"><path fill="#555" d="M6.6 10.8a15 15 0 0 0 6.6 6.6l2.2-2.2c.3-.3.7-.4 1-.2 1.1.4 2.3.6 3.6.6.6 0 1 .4 1 1V20c0 .6-.4 1-1 1A17 17 0 0 1 3 4c0-.6.4-1 1-1h3.5c.6 0 1 .4 1 1 0 1.3.2 2.5.6 3.6.1.3 0 .7-.2 1z"/></svg>(970) 555-0142</span>
      <span><svg width="13" height="10" viewBox="0 0 24 18" aria-hidden="true"><path fill="#555" d="M0 0h24v18H0z"/><path fill="none" stroke="#ddedf4" stroke-width="2" d="M1 1l11 9 11-9"/></svg>studio@pineroverslane.com</span>
    </div>
    <a class="hero-button" href="#">EXPLORE GALLERY</a>
  </section>

  <section class="featured-piece">
    <div class="piece-photo" role="img" aria-label="Photograph of a mounted amethyst geode on a stone and wood base"></div>
    <div class="piece-info">
      <h2 class="piece-title">Amethyst Geode Mounted</h2>
      <h3 class="piece-label">Product Story:</h3>
      <p class="piece-story">Lorem ipsum dolor sit amet, consectetur adipisicing elit, sed do eiusmod tempor incididunt ut labore et dolore magna aliqua. Ut enim ad minim veniam, quis nostrud exercitation ullamco laboris nisi ut aliquip ex ea commodo consequat. Duis aute irure dolor in reprehenderit in voluptate velit</p>
      <h3 class="piece-label">Materials:</h3>
      <p class="piece-materials">Amethyst Crystal, Gold Mounting Plates, Kauri Wood Base</p>
      <p class="piece-price">$1299.00</p>
    </div>
  </section>

  <div class="next-piece" role="img" aria-label="Photograph of the next featured sculpture"></div>
</body>
</html>
```